Basic business card

use my newly created logo - and the phrases (Lower Cost of Test & Accelarated New Product Introduction) - and my new email domain / ID - use at conferences / tradeshows

Industry/Entity Type

semiconductor

Contact Information for Business Card

Daniel K Forde, Owner, communicate via Logo - Lower COT - Cost of Test, Accelerated NPI - New Product Introduction, phone +1 555 613 0946, Chandler, Arizona, USA, daniel.forde@qal-vub.com

Font styles to use
Sans Serif

Requirements
Nice to have
• re-use my logo created via Pixel Harbor last August (#7315926)

```html
<!DOCTYPE html>
<html lang="en">
<head>
<meta charset="utf-8">
<title>QAL-VUB Business Card</title>
<link href="https://fonts.googleapis.com/css2?family=Open+Sans:wght@400;600;700&display=swap" rel="stylesheet">
<style>
  :root {
    --stage: #333333;
    --navy-light: #243546;
    --navy-dark: #0d141c;
    --steel: #a9bccf;
    --slate: #3f4a66;
    --orange: #f39a1e;
    --green: #7cc142;
    --ink: #1a1a1a;
    --paper: #ffffff;
  }
  * { margin: 0; padding: 0; box-sizing: border-box; }
  html, body { width: 1200px; height: 780px; overflow: hidden; }
  body {
    background: var(--stage);
    font-family: "Open Sans", Arial, sans-serif;
    display: flex;
    align-items: center;
    justify-content: center;
    gap: 40px;
  }
  .card {
    position: relative;
    width: 540px;
    height: 309px;
    overflow: hidden;
  }
  /* Front side */
  .card-front {
    background: radial-gradient(ellipse at 60% 35%, var(--navy-light), var(--navy-dark) 85%);
    display: flex;
    align-items: center;
    justify-content: center;
  }
  .brand {
    display: flex;
    align-items: center;
    gap: 12px;
    font-weight: 600;
    letter-spacing: 1px;
  }
  .brand-mark { display: block; width: 14px; height: 14px; }
  .card-front .brand { font-size: 54px; color: var(--steel); }
  .card-front .brand-mark { width: 22px; height: 22px; background: var(--steel); }
  /* Back side */
  .card-back { background: var(--paper); }
  .card-back .brand {
    position: absolute;
    left: 34px;
    top: 142px;
    font-size: 34px;
    color: var(--slate);
  }
  .card-back .brand-mark { width: 16px; height: 16px; background: var(--slate); }
  .divider {
    position: absolute;
    left: 292px;
    top: 60px;
    width: 1px;
    height: 165px;
    background: var(--ink);
  }
  .contact {
    position: absolute;
    left: 310px;
    top: 70px;
  }
  .person-name { font-size: 23px; font-weight: 700; line-height: 1.1; }
  .person-name .first { color: var(--orange); }
  .person-name .last { color: var(--green); }
  .person-title { font-size: 12.5px; font-weight: 600; color: var(--ink); margin-top: 2px; }
  .contact-list { list-style: none; margin-top: 16px; }
  .contact-list li {
    display: flex;
    align-items: center;
    gap: 8px;
    font-size: 13px;
    color: var(--ink);
    line-height: 22px;
  }
  .contact-list svg { width: 13px; height: 13px; flex: none; }
  .band-accent {
    position: absolute;
    left: 400px;
    right: 0;
    top: 222px;
    height: 22px;
    background: var(--orange);
  }
  .band-address {
    position: absolute;
    left: 0;
    width: 430px;
    top: 252px;
    height: 26px;
    background: var(--green);
    color: var(--paper);
    font-size: 13px;
    font-weight: 600;
    line-height: 26px;
    padding-left: 40px;
    letter-spacing: 0.3px;
  }
</style>
</head>
<body>
  <section class="card card-front">
    <div class="brand"><span class="brand-mark"></span>QAL-VUB</div>
  </section>

  <section class="card card-back">
    <div class="brand"><span class="brand-mark"></span>QAL-VUB</div>
    <div class="divider"></div>
    <div class="contact">
      <p class="person-name"><span class="first">Lena</span> <span class="last">Varkova</span></p>
      <p class="person-title">Managing Director</p>
      <ul class="contact-list">
        <li>
          <svg viewBox="0 0 24 24" aria-hidden="true"><path fill="#f39a1e" d="M6.6 10.8a15.1 15.1 0 0 0 6.6 6.6l2.2-2.2a1 1 0 0 1 1-.25 11.4 11.4 0 0 0 3.6.57 1 1 0 0 1 1 1V20a1 1 0 0 1-1 1A17 17 0 0 1 3 4a1 1 0 0 1 1-1h3.5a1 1 0 0 1 1 1c0 1.25.2 2.45.57 3.57a1 1 0 0 1-.25 1z"/></svg>
          (555) 204-7781
        </li>
        <li>
          <svg viewBox="0 0 24 24" aria-hidden="true"><rect x="2" y="5" width="20" height="14" rx="1.5" fill="#f39a1e"/><path d="M3 6l9 7 9-7" fill="none" stroke="#fff" stroke-width="1.8"/></svg>
          info@qal-vub.com
        </li>
        <li>
          <svg viewBox="0 0 24 24" aria-hidden="true"><circle cx="12" cy="12" r="10" fill="#f39a1e"/><path d="M2 12h20M12 2c3 3 3 17 0 20M12 2c-3 3-3 17 0 20" fill="none" stroke="#fff" stroke-width="1.4"/></svg>
          www.qal-vub.com
        </li>
      </ul>
    </div>
    <div class="band-accent"></div>
    <div class="band-address">1180 Harbor Lane Suite 310 Mesa, AZ 85201</div>
  </section>
</body>
</html>
```